Signage Design Project

Busisness is a bakery and deli long time owned by the Tavel family. Want to develop a new outside sign that communicates it is a deli and a bakery but keeps the tavel name in the design.

The sign when produced will be about 10' by 3' . It is not lighted at present but could be if it were advantageous.

The name of the store is:

Tavel's Harbor Lane Bakery and Deli. The concept is to have a new,modern sign that reinforces that it is a deli and a bakery, as most people only know about the bakery side of the business
Updates

The name Tavel is just a reinforcer so the people kno it is still in the family.  The emphasis should be on the HARBOR LANE BAKERY and DELI

Target Market(s)

Small business breakfast and lunch customers

Industry/Entity Type

Bakery

Requirements
Must have
• Great impact from the road. Communicate that it is a deli and a bakery. Keep the Tavel name but need not be a major design element

```html
<!DOCTYPE html>
<html lang="en">
<head>
<meta charset="utf-8">
<title>Tavel's Harbor Lane Bakery and Deli – Storefront Sign</title>
<link rel="stylesheet" href="https://fonts.googleapis.com/css2?family=Francois+One&family=Tinos:wght@700&display=swap">
<style>
  :root {
    --sign-red: #b5151c;
    --band-maroon: #7a1218;
    --gold-light: #f6e3a0;
    --gold-deep: #c9a24a;
    --text-white: #ffffff;
  }
  html, body {
    margin: 0;
    padding: 0;
    width: 1200px;
    height: 361px;
    overflow: hidden;
    background: #ffffff;
  }
  .sign {
    position: relative;
    width: 1200px;
    height: 361px;
    background: var(--sign-red);
    overflow: hidden;
  }
  .name-band {
    position: absolute;
    left: 0;
    top: 46px;
    width: 1200px;
    height: 266px;
    background: var(--band-maroon);
  }
  .band-rule {
    position: absolute;
    left: 330px;
    width: 540px;
    height: 3px;
    background: linear-gradient(90deg, transparent, var(--gold-deep) 25%, var(--gold-light) 50%, var(--gold-deep) 75%, transparent);
  }
  .band-rule--top { top: 45px; }
  .band-rule--bottom { top: 310px; }
  .flourish {
    position: absolute;
    left: 470px;
    width: 260px;
    background: radial-gradient(ellipse at center, var(--gold-light) 0%, var(--gold-deep) 55%, rgba(201,162,74,0) 100%);
    opacity: 0.85;
  }
  .flourish--top { top: 0; height: 56px; }
  .flourish--bottom { top: 306px; height: 55px; }
  .family-line {
    position: absolute;
    left: 0;
    top: 82px;
    width: 1200px;
    text-align: center;
    font-family: "Francois One", "Arial Narrow", sans-serif;
    color: var(--text-white);
    line-height: 1;
    white-space: nowrap;
  }
  .family-name {
    font-size: 34px;
    margin-right: 8px;
  }
  .location-name {
    font-size: 50px;
  }
  .business-type {
    position: absolute;
    left: 0;
    top: 112px;
    width: 1200px;
    text-align: center;
    font-family: "Tinos", "Times New Roman", serif;
    font-weight: 700;
    font-size: 148px;
    line-height: 1;
    letter-spacing: 0;
    color: var(--text-white);
    white-space: nowrap;
    transform: scaleY(1.22);
    transform-origin: top center;
  }
</style>
</head>
<body>
  <div class="sign">
    <div class="name-band"></div>
    <div class="band-rule band-rule--top"></div>
    <div class="band-rule band-rule--bottom"></div>
    <div class="flourish flourish--top" role="img" aria-label="Gold scrollwork ornament centred on the top edge of the band"></div>
    <div class="flourish flourish--bottom" role="img" aria-label="Gold scrollwork ornament centred on the bottom edge of the band"></div>
    <div class="family-line">
      <span class="family-name">Tavel's</span><span class="location-name">Harbor Lane</span>
    </div>
    <div class="business-type">Bakery and Deli</div>
  </div>
</body>
</html>
```